Website Design for a Project Management Consulting Business

I have a logo design already and now I need a website.
I am a project manager and run my own consulting business.
Currently I am under contract with 3 major Vantage 400 companies. I'd like a website I can direct current and future clients.
My job is running IT projects and working with developers to deliver business priorities.
The website should be professional and clean - I work IT projects and would like to incorporate that into any theme.
I'd like the site to have several page or breakoff links - sections would include : about me, about my services, a page to display all of my certification badges, another page to talk about highlights from past projects and so on.
Looking for a collaborative experience.

Industry/Entity Type

Vantage 400 Consulting Firm - Project Management

Coding

Coded - Design and coding required

Number of Pages Required

1 page

Font styles to use
Serif

Colors
0094D4
00A9DD
6FCCEA
C7EBF8
E9F6FB
EE7325
F08F49
F5BC92
FAE3D3
FDF4ED

Requirements
Must have
• Sections that are a must: About Me (bio), About My Services, About my Certifications and Credentials, Experience on Past Projects,
Nice to have
• I have added the logo below - I'd like to use the logo and have it prominent ; should be professional and inviting

```html
<!DOCTYPE html>
<html lang="en">
<head>
<meta charset="utf-8">
<title>Meridian — Project Management Consulting</title>
<link href="https://fonts.googleapis.com/css2?family=Montserrat:wght@700;800&family=Mulish:wght@400;600;700;800&display=swap" rel="stylesheet">
<style>
:root{
  --blue:#0094D4;
  --blue-mid:#1a95d8;
  --blue-light:#6FCCEA;
  --orange:#EE7325;
  --orange-soft:#F08F49;
  --peach:#F5BC92;
  --ink:#222;
  --text:#555;
  --grey-bg:#f3f3f3;
  --footer:#1d1d1f;
  --navy:#123a6b;
}
*{margin:0;padding:0;box-sizing:border-box}
html,body{width:1200px;height:4232px;overflow:hidden}
body{position:relative;font-family:"Mulish",sans-serif;color:var(--ink);background:#fff}
.abs{position:absolute}
.heading{font-family:"Montserrat",sans-serif;font-weight:800;font-size:38px;text-align:center;letter-spacing:.5px;color:var(--blue)}
.heading span{color:var(--orange)}
.btn{position:absolute;background:var(--orange);color:#fff;font-weight:800;font-size:14px;border-radius:22px;display:flex;align-items:center;justify-content:center;gap:6px;box-shadow:0 4px 10px rgba(238,115,37,.35);letter-spacing:.3px}
.btn::after{content:"›";display:inline-flex;width:13px;height:13px;border-radius:50%;background:#fff;color:var(--orange);font-size:12px;line-height:12px;justify-content:center}
.photo{position:absolute}

/* header */
.site-header{position:absolute;left:0;top:0;width:1200px;height:104px;border-top:4px solid var(--orange);background:#fff}
.brand{position:absolute;left:88px;top:30px;display:flex;align-items:center;gap:12px}
.brand-mark{width:40px;height:40px;border:3px solid var(--navy)}
.brand-name{font-family:"Mulish",sans-serif;font-weight:800;font-size:34px;color:var(--navy);letter-spacing:1px}
.nav{position:absolute;top:44px;left:390px;font-size:14px;font-weight:600;color:#333}
.nav a{position:absolute;white-space:nowrap;color:#333;text-decoration:none}
.nav .active{color:var(--orange)}
.call{position:absolute;left:930px;top:32px;display:flex;align-items:center;gap:16px}
.call-icon{width:42px;height:42px;border-radius:50%;background:var(--orange);display:flex;align-items:center;justify-content:center}
.call-text{font-size:14px;line-height:22px;color:#333}
.call-text b{font-size:17px;font-weight:700}

/* hero */
.hero{position:absolute;left:0;top:104px;width:1200px;height:686px;background:linear-gradient(90deg,#f1f1f1,#f7f7f7);overflow:hidden}
.hero-photo{left:470px;top:0;width:730px;height:686px;border-top-right-radius:300px;background:linear-gradient(135deg,#e6e2dd 0%,#c9b49a 35%,#3e5d88 60%,#d9d6d2 100%)}
.hero-band{position:absolute;left:1010px;top:0;width:190px;height:6px;background:var(--orange)}
.hero-copy{position:absolute;left:120px;top:156px;width:500px;text-align:center}
.welcome{font-family:"Montserrat",sans-serif;font-weight:700;font-size:15px;letter-spacing:5px;display:flex;align-items:center;justify-content:center;gap:12px}
.welcome::before,.welcome::after{content:"";width:78px;height:2px;background:var(--orange)}
.hero-title{font-family:"Montserrat",sans-serif;font-weight:800;font-size:74px;letter-spacing:2px;color:#222;margin-top:2px;line-height:86px}
.hero-sub{font-weight:700;font-size:17px;margin-top:6px}
.dots{position:absolute;display:flex;gap:8px}
.dots i{width:11px;height:11px;border:1.5px solid #555;border-radius:50%}
.dots i.on{border-color:var(--orange);box-shadow:inset 0 0 0 2px #fff;background:var(--orange)}

/* services */
.card{position:absolute;top:928px;width:310px;height:382px;background:#fff;box-shadow:0 4px 18px rgba(0,0,0,.1)}
.card .photo{left:0;top:0;width:310px;height:190px}
.card h3{position:absolute;left:22px;top:206px;font-size:21px;font-weight:600;color:#222}
.card p{position:absolute;left:22px;top:245px;width:275px;font-size:13.5px;line-height:26px;color:#666}
.arrow-pill{position:absolute;left:22px;top:336px;width:60px;height:20px;border-radius:10px;background:var(--blue)}
.card.featured{height:407px;z-index:2}
.dot-grid{left:423px;top:1212px;width:352px;height:150px;background-image:radial-gradient(#888 1.3px,transparent 1.5px);background-size:16px 16px}

/* about */
.about{position:absolute;left:0;top:1422px;width:1200px;height:531px;background:var(--blue-mid)}
.about-text{position:absolute;left:616px;top:70px;width:472px;color:#fff}
.about-text h2{font-family:"Montserrat",sans-serif;font-weight:800;font-size:40px;margin-bottom:18px}
.about-text p{font-size:14px;line-height:26px;text-align:justify;margin-bottom:26px}

/* certs */
.badge-label{position:absolute;width:260px;text-align:center;font-weight:700;font-size:18px;line-height:30px;color:#222}
.divider{position:absolute;width:8px;height:210px;background:var(--blue);transform:skewX(-9deg)}

/* projects */
.projects{position:absolute;left:0;top:2450px;width:1200px;height:591px;background:linear-gradient(180deg,#f6f6f6,#ececec)}
.nav-arrow{position:absolute;width:34px;height:34px;border-radius:50%;background:#fff;display:flex;align-items:center;justify-content:center;font-size:20px;font-weight:800;color:#222;box-shadow:0 2px 6px rgba(0,0,0,.2)}

/* stories */
.circle{position:absolute;border-radius:50%}
.quote{position:absolute;left:400px;top:3618px;width:400px;text-align:center;font-size:14px;line-height:26px;color:#444}

/* footer */
.footer{position:absolute;left:0;top:3806px;width:1200px;height:426px;background:#fff;color:#fff}
.footer-shape{position:absolute;left:0;top:0;width:1200px;height:426px;background:linear-gradient(180deg,#202022,#151516);border-top-left-radius:200px}
.footer-band{position:absolute;left:0;top:0;width:190px;height:6px;background:var(--orange)}
.f-col{position:absolute;top:88px}
.f-col h4{font-size:21px;font-weight:600;margin-bottom:24px}
.f-col p,.f-col li{font-size:14px;line-height:25px;color:#eee;list-style:none}
.f-col li{line-height:31px}
.contact-row{display:flex;align-items:center;gap:14px;font-size:14px;margin-bottom:38px}
.social{position:absolute;top:4052px;display:flex;gap:6px}
.social i{width:30px;height:30px;border-radius:50%;background:var(--blue)}
.social i.alt{background:var(--orange)}
.email{position:absolute;left:828px;top:124px;width:260px;height:42px;background:#fff;color:#888;font-size:13px;padding:12px 14px}
.subscribe{position:absolute;left:828px;top:176px;width:260px;height:43px;background:var(--orange);font-size:14px;font-weight:700;display:flex;align-items:center;justify-content:center}
.copyright{position:absolute;left:0;top:378px;width:1200px;text-align:center;font-size:13px}
</style>
</head>
<body>

<header class="site-header">
  <div class="brand"><div class="brand-mark"></div><div class="brand-name">MERIDIAN</div></div>
  <nav class="nav">
    <a class="active" style="left:0">Home</a>
    <a style="left:73px">About me</a>
    <a style="left:172px">Services</a>
    <a style="left:260px">Blog</a>
    <a style="left:321px">Testimonials</a>
    <a style="left:439px">Contact us</a>
  </nav>
  <svg class="abs" style="left:390px;top:62px" width="52" height="10"><path d="M0 5H46M40 1l6 4-6 4" stroke="#EE7325" stroke-width="2" fill="none"/></svg>
  <div class="call">
    <div class="call-icon"><svg width="16" height="16" viewBox="0 0 24 24"><path fill="#fff" d="M6.6 10.8a15 15 0 006.6 6.6l2.2-2.2c.3-.3.7-.4 1-.2 1.1.4 2.3.6 3.6.6.6 0 1 .4 1 1V20c0 .6-.4 1-1 1A17 17 0 013 4c0-.6.4-1 1-1h3.5c.6 0 1 .4 1 1 0 1.3.2 2.5.6 3.6.1.3 0 .7-.2 1z"/></svg></div>
    <div class="call-text">Call us Today:<br><b>+1 555 010 2040</b></div>
  </div>
</header>

<section class="hero">
  <div class="photo hero-photo" role="img" aria-label="Business team shaking hands and celebrating around a laptop in a bright office"></div>
  <div class="hero-band"></div>
  <div class="hero-copy">
    <div class="welcome">WELCOME TO</div>
    <div class="hero-title">MERIDIAN</div>
    <div class="hero-sub">Project Management Consulting Business</div>
  </div>
  <div class="btn" style="left:285px;top:309px;width:167px;height:42px">GET STARTED</div>
  <div class="dots" style="left:334px;top:590px"><i></i><i class="on"></i><i></i><i></i></div>
</section>

<section aria-label="Our services">
  <h2 class="heading abs" style="left:0;top:862px;width:1200px">OUR <span>SERVICES</span></h2>
  <div class="photo dot-grid"></div>
  <article class="card" style="left:111px">
    <div class="photo" role="img" aria-label="Team meeting around a boardroom table with city windows" style="background:linear-gradient(135deg,#c9d3da,#7a8790 55%,#3b3f45)"></div>
    <h3>Duis aute irure</h3>
    <p>Lorem ipsum dolor sit amet, consecte tur adipiscing elit, sed do eiusmod tem por incididunt ut labore</p>
    <svg class="arrow-pill" viewBox="0 0 60 20"><path d="M18 10h22M35 6l5 4-5 4" stroke="#fff" stroke-width="2" fill="none"/></svg>
  </article>
  <article class="card featured" style="left:445px">
    <div class="photo" role="img" aria-label="Hands working on a laptop beside printed charts" style="background:linear-gradient(135deg,#8c7e6e,#d4d6d9 50%,#9fb8cc)"></div>
    <h3>Duis aute irure</h3>
    <p>Lorem ipsum dolor sit amet, consecte tur adipiscing elit, sed do eiusmod tem por incididunt ut labore</p>
    <div class="btn" style="left:22px;top:334px;width:166px;height:40px">LEARN MORE</div>
  </article>
  <article class="card" style="left:778px">
    <div class="photo" role="img" aria-label="Two consultants discussing at a desk" style="background:linear-gradient(135deg,#b7aa9a,#5c544d 55%,#d9d2c8)"></div>
    <h3>Duis aute irure</h3>
    <p>Lorem ipsum dolor sit amet, consecte tur adipiscing elit, sed do eiusmod tem por incididunt ut labore</p>
    <svg class="arrow-pill" viewBox="0 0 60 20"><path d="M18 10h22M35 6l5 4-5 4" stroke="#fff" stroke-width="2" fill="none"/></svg>
  </article>
</section>

<section class="about">
  <div class="photo" role="img" aria-label="Portrait of the consultant in a blue suit holding a tablet" style="left:111px;top:81px;width:469px;height:362px;background:linear-gradient(135deg,#d9dcde,#9aa6b1 45%,#24406a 70%,#e3e4e5)"></div>
  <div class="photo" style="left:90px;top:340px;width:128px;height:126px;border:7px solid var(--navy)"></div>
  <div class="about-text">
    <h2>ABOUT ME</h2>
    <p>Daniel Harlow is the Owner of Project Management Meridian, LLC and serves as Principal Lead Consultant on waterfall and agile contract opportunities.</p>
    <p>Project Management Meridian, LLC has engaged on a contract basis with Vantage 400 companies across various industries including banking and credit unions, global supply chain, and international food distribution. Dan Harlow brings 12 years of experience to his clients encompassing various project methodologies including: waterfall</p>
  </div>
  <div class="btn" style="left:616px;top:405px;width:164px;height:40px">LEARN MORE</div>
  <div class="photo" role="img" aria-label="Handwritten signature of Dan Harlow" style="left:800px;top:405px;width:140px;height:36px;background:linear-gradient(90deg,rgba(255,255,255,.22),rgba(255,255,255,.08))"></div>
</section>

<section aria-label="Certifications">
  <h2 class="heading abs" style="left:0;top:2028px;width:1200px;line-height:40px">ABOUT MY CERTIFICATIONS<br><span>AND CREDENTIALS</span></h2>
  <div class="circle" style="left:198px;top:2155px;width:150px;height:150px;background:radial-gradient(circle,#f9c234 55%,#f2a516 56%)"></div>
  <div class="circle" style="left:527px;top:2155px;width:150px;height:150px;background:radial-gradient(circle,#F08F49 55%,#EE7325 56%)"></div>
  <div class="circle" style="left:853px;top:2155px;width:150px;height:150px;background:radial-gradient(circle,#f9c234 55%,#f2a516 56%)"></div>
  <div class="divider" style="left:442px;top:2157px"></div>
  <div class="divider" style="left:772px;top:2157px"></div>
  <div class="badge-label" style="left:143px;top:2310px">Certified<br>Sprint Leader</div>
  <div class="badge-label" style="left:472px;top:2310px">Certified Sprint<br>Product Owner</div>
  <div class="badge-label" style="left:798px;top:2310px">Advanced - Certified<br>Sprint Leader</div>
</section>

<section class="projects">
  <h2 class="heading abs" style="left:0;top:74px;width:1200px">OUR PAST <span>PROJECTS</span></h2>
  <div class="photo" role="img" aria-label="Colleagues reviewing a document in a cafe" style="left:14px;top:185px;width:326px;height:245px;background:linear-gradient(135deg,#4d3b2e,#a08066 50%,#3a2f28)"></div>
  <div class="photo" role="img" aria-label="Two women in conversation at a meeting" style="left:854px;top:185px;width:326px;height:245px;background:linear-gradient(135deg,#c8c5c0,#8e7a68 50%,#2f3640)"></div>
  <div class="photo" style="left:357px;top:150px;width:480px;height:322px;background:#e3e4e6;border-radius:12px 12px 4px 4px;box-shadow:0 20px 24px -14px rgba(0,0,0,.35)"></div>
  <div class="photo" role="img" aria-label="Top view of a team working with laptops and charts on a table" style="left:380px;top:172px;width:433px;height:271px;background:linear-gradient(135deg,#cfc5b6,#7d8a96 45%,#e8e2d6 70%,#4a4f57)"></div>
  <div class="nav-arrow" style="left:233px;top:285px">‹</div>
  <div class="nav-arrow" style="left:931px;top:285px">›</div>
</section>

<section aria-label="Success stories">
  <h2 class="heading abs" style="left:0;top:3122px;width:1200px">SUCCESS <span>STORIES</span></h2>
  <div class="abs" style="left:0;top:3190px;width:1200px;text-align:center;font-weight:700;font-size:16px">John Doe</div>
  <div class="circle" role="img" aria-label="Two smiling senior professionals" style="left:114px;top:3270px;width:274px;height:274px;background:linear-gradient(135deg,#d4c8bb,#34404f 55%,#e0d9d2)"></div>
  <div class="circle" role="img" aria-label="Smiling businessman with arms crossed" style="left:425px;top:3230px;width:350px;height:350px;background:linear-gradient(135deg,#d9d9d9,#90a8c4 50%,#2c3747);box-shadow:0 6px 16px rgba(0,0,0,.25)"></div>
  <div class="circle" role="img" aria-label="Businesswoman holding a folder in an office" style="left:813px;top:3270px;width:274px;height:274px;background:linear-gradient(135deg,#7fa1c4,#d7c7b3 50%,#2a2f3a)"></div>
  <div class="circle" style="left:571px;top:3374px;width:58px;height:58px;background:var(--orange);display:flex;align-items:center;justify-content:center"><svg width="18" height="20"><path d="M3 1l14 9-14 9z" fill="#fff"/></svg></div>
  <div class="abs" style="left:599px;top:3580px;width:2px;height:40px;background:var(--orange)"></div>
  <p class="quote">“ Lorem ipsum dolor sit amet, consectetur &nbsp;elit, sed tempor incididunt ut labore et dolore”</p>
  <div class="dots" style="left:568px;top:3710px"><i></i><i class="on"></i><i></i><i></i></div>
</section>

<footer class="footer">
  <div class="footer-shape"></div>
  <div class="footer-band"></div>
  <div class="f-col" style="left:110px;width:265px">
    <h4>About Company</h4>
    <p>Lorem ipsum dolor sit amet, conse ctetur adipiscing elit, sed do eiusm od tempor incididunt ut labore et dolore magna aliqua.</p>
  </div>
  <div class="f-col" style="left:417px">
    <h4>Useful Links</h4>
    <ul><li>Home</li><li>Our Services</li><li>About Me</li><li>Success Story</li><li>Contact</li></ul>
  </div>
  <div class="f-col" style="left:587px">
    <h4>Contact</h4>
    <div class="contact-row"><svg width="12" height="12" viewBox="0 0 24 24"><path fill="#fff" d="M6.6 10.8a15 15 0 006.6 6.6l2.2-2.2c.3-.3.7-.4 1-.2 1.1.4 2.3.6 3.6.6.6 0 1 .4 1 1V20c0 .6-.4 1-1 1A17 17 0 013 4c0-.6.4-1 1-1h3.5c.6 0 1 .4 1 1 0 1.3.2 2.5.6 3.6.1.3 0 .7-.2 1z"/></svg>+1 555 010 2040</div>
    <div class="contact-row"><svg width="13" height="10"><rect x=".5" y=".5" width="12" height="9" fill="#fff"/><path d="M1 1l5.5 4.5L12 1" stroke="#1d1d1f" fill="none"/></svg>info@meridianpm.com</div>
    <div class="contact-row"><svg width="10" height="14" viewBox="0 0 10 14"><path d="M5 0a5 5 0 015 5c0 4-5 9-5 9S0 9 0 5a5 5 0 015-5z" fill="#fff"/><circle cx="5" cy="5" r="2" fill="#1d1d1f"/></svg>48 Harbor Lane, NY</div>
  </div>
  <div class="f-col" style="left:825px"><h4>Subscribe Newsletter</h4></div>
  <div class="email">Email Address</div>
  <div class="subscribe">SUBSCRIBE US</div>
  <div class="abs" style="left:110px;top:352px;width:978px;height:1px;background:#555"></div>
  <div class="copyright">© Copyright 2022 Company name, All Rights Reserved.</div>
</footer>
<div class="social" style="left:107px"><i></i><i></i><i class="alt"></i><i></i></div>

</body>
</html>
```